Luxury Wine Label for New Startup Winery

We need a wine label for our new winery startup. We have worked with a local designer but do not feel the resulting label / logo have the elevation required to present our brand as a luxury wine. Our winery is called "Quailbrook Vineyards" and we are focused on extremely high quality hand crafted artisan and estate wines from the Pacific Northwest.
We would like to see designs that utilize a tree line, or other imagery that represents the "Quailbrook" part of our company name. Another interesting feature could be wood grain.
A logo will be required based on your design so please design with this in mind:
This logo should be consistent with the wine bottle label design, and should be representative of our high end exclusive wine while giving a sense of place (Oregon/ Pacific Northwest.)
I will supply an image of the design we received from our local designer, PLEASE NOTE: in general we do like wood grain and tree line concepts but feel the execution was poorly done.
ATTN: Logo design should be suitable for use on: Bottles (Red wine/rose/white wine), Bussiness cards, vehicle signage, business signage, etc
P.S.:
If you have a design that is not outside the box we are still interested in seeing it.
Label is for a burgundy style bottle with a label height of 3.5 - 4" and a width of 3.5-4"
any label <= 4"x4" and >=3.5"x3.5" will be acceptable:
HOWEVER Width should be greater than or equal to height due to the bottle format
Target Market(s)
Wine enthusiasts with adequate discretionary budgets to afford $100 bottles of wine.
Industry/Entity Type
Wine / Winery
Requirements
Must have
- A sense of luxury, a feel of exclusivity, and a theme consistent with our product and brand name
Nice to have
- Tree line, wood grain or other wood themes. Serif fonts
Should not have
- anything cheesy, off topic, hard to read script fonts or anything that makes the label hard to read from a few feet away or too busy

```html
<!DOCTYPE html>
<html lang="en">
<head>
<meta charset="utf-8">
<title>Quailbrook Vineyards – Syrah Labels</title>
<link rel="stylesheet" href="https://fonts.googleapis.com/css2?family=Josefin+Sans:wght@400;600;700&display=swap">
<style>
  :root {
    --backdrop: #e4e4e4;
    --label-white: #f4f3f1;
    --wood-dark: #33231a;
    --wood-mid: #4b3426;
    --wood-light: #5c4231;
    --treeline-top: #d9d3cc;
    --ink: #2a2624;
    --ink-soft: #3d3835;
    --type-light: #f3efe9;
    --seal-gold: #c48a2c;
    --seal-red: #a3172b;
  }
  * { box-sizing: border-box; margin: 0; padding: 0; }
  html, body {
    width: 1200px;
    height: 900px;
    overflow: hidden;
    background: var(--backdrop);
    font-family: "Josefin Sans", "Helvetica Neue", Arial, sans-serif;
  }
  .label-set {
    position: absolute;
    inset: 0;
    display: flex;
    justify-content: center;
    align-items: flex-start;
    gap: 80px;
    padding-top: 240px;
  }
  .wine-label {
    position: relative;
    width: 500px;
    height: 480px;
    border-radius: 22px;
    background: var(--label-white);
    box-shadow: 0 2px 10px rgba(0,0,0,0.12);
  }
  .wood-panel {
    position: absolute;
    left: 0; right: 0; top: 0;
    height: 250px;
    border-radius: 22px 22px 0 0;
    background: linear-gradient(90deg, var(--wood-dark) 0%, var(--wood-mid) 30%, var(--wood-light) 50%, var(--wood-mid) 70%, var(--wood-dark) 100%);
  }
  .tree-line {
    position: absolute;
    left: 0; right: 0;
    top: 250px;
    height: 64px;
    background: linear-gradient(180deg, var(--treeline-top) 0%, var(--label-white) 100%);
  }
  .brand-seal {
    position: absolute;
    left: 50%;
    top: -55px;
    width: 150px;
    height: 150px;
    margin-left: -75px;
    border-radius: 50%;
  }
  .wine-label--gold .brand-seal { background: var(--seal-gold); }
  .wine-label--red .brand-seal { background: var(--seal-red); }
  .brand-name {
    position: absolute;
    left: 0; right: 0;
    top: 128px;
    text-align: center;
    color: var(--type-light);
    font-weight: 600;
  }
  .brand-name__primary {
    display: block;
    font-size: 48px;
    letter-spacing: 3px;
    line-height: 1;
  }
  .brand-name__secondary {
    display: block;
    margin-top: 8px;
    font-size: 23px;
    font-weight: 400;
    letter-spacing: 7px;
    line-height: 1;
  }
  .varietal {
    position: absolute;
    left: 0; right: 0;
    top: 334px;
    text-align: center;
    color: var(--ink);
    font-size: 50px;
    font-weight: 600;
    letter-spacing: 10px;
    line-height: 1;
  }
  .appellation {
    position: absolute;
    left: 0; right: 0;
    top: 404px;
    text-align: center;
    color: var(--ink-soft);
    font-size: 19px;
    font-weight: 400;
    letter-spacing: 1.5px;
    line-height: 1.45;
  }
</style>
</head>
<body>
  <main class="label-set">
    <article class="wine-label wine-label--gold">
      <div class="wood-panel" role="img" aria-label="Dark vertical wood grain background"></div>
      <div class="tree-line" role="img" aria-label="White pine tree line silhouette"></div>
      <div class="brand-seal" aria-hidden="true"></div>
      <h1 class="brand-name">
        <span class="brand-name__primary">QUAILBROOK</span>
        <span class="brand-name__secondary">VINEYARDS</span>
      </h1>
      <p class="varietal">SYRAH</p>
      <p class="appellation">WILLAMETTE VALLEY<br>2024</p>
    </article>

    <article class="wine-label wine-label--red">
      <div class="wood-panel" role="img" aria-label="Dark vertical wood grain background"></div>
      <div class="tree-line" role="img" aria-label="White pine tree line silhouette"></div>
      <div class="brand-seal" aria-hidden="true"></div>
      <h2 class="brand-name">
        <span class="brand-name__primary">QUAILBROOK</span>
        <span class="brand-name__secondary">VINEYARDS</span>
      </h2>
      <p class="varietal">SYRAH</p>
      <p class="appellation">WILLAMETTE VALLEY<br>2024</p>
    </article>
  </main>
</body>
</html>
```